Corvana Tongue Works, LLC

We need a business card that includes information about our business and conveys a reliable business that provides document translation services and interpreters for a variety of corporate and individual clients. We want to come across as professional, reliable, yet approachable. It should include the following on one side:

ESL / ENL Language Classes, Private Lessons, and Online Tutors
PLEXA Training and Testing
Translating & Interpreting Services
Contact us about Over-the-Phone Interpreting in over 200 languages
24/7/365
www.corvanatongue.example

The other side should include (555) 481-3062

Rhoda Pelling, President
482 Garnet Ave., Ste. 219
Indianapolis, IN 40917

Please add USA as part of the address. Also, please add rmpelling@corvanatongueworks.example as the e-mail address. Thank you.

Target Market(s)

Business professionals, their families, the international community

Industry/Entity Type

Business

Contact Information for Business Card

24/7/365
www.corvanatongue.example

(555) 481-3062

Rhoda Pelling, President
482 Garnet Ave., Ste. 219
Indianapolis, IN 40917
USA

Font styles to use
Sans Serif

Colors

Designer to choose colors to be used in the design.

Requirements
Must have
• See project description
• e-mail address and web address
• Phone number
Nice to have
• a globe
• physical address
Should not have
• Should not have the same color scheme as other agencies in our market in Indiana unless it is blue and black. No purple or yellow.

```html
<!DOCTYPE html>
<html lang="en">
<head>
<meta charset="utf-8">
<title>Corvana Tongue Works — Business Card</title>
<link rel="stylesheet" href="https://fonts.googleapis.com/css2?family=Lato:wght@400;700&display=swap">
<style>
  :root {
    --brand-blue: #2a96d6;
    --brand-blue-light: #5fb3e6;
    --ink: #1d1d1d;
    --ink-soft: #3a3a3a;
    --paper: #ffffff;
    --backdrop: #e6e7e9;
    --rule: #d4d4d4;
  }
  * { box-sizing: border-box; margin: 0; padding: 0; }
  html, body {
    width: 1200px; height: 900px; overflow: hidden;
    background: var(--backdrop);
    font-family: "Lato", Arial, sans-serif;
  }
  .card {
    position: absolute; top: 295px;
    width: 540px; height: 310px;
    overflow: hidden;
    box-shadow: 0 6px 18px rgba(0,0,0,.18);
  }
  /* Front */
  .card--front { left: 40px; background: var(--paper); }
  .brand-lockup {
    position: absolute; left: 26px; top: 112px;
    display: flex; align-items: center; gap: 12px;
  }
  .brand-lockup__dot {
    width: 82px; height: 82px; border-radius: 50%;
    background: var(--brand-blue); flex: none;
  }
  .brand-lockup__name {
    font-size: 21px; line-height: 1.05; font-weight: 400;
    color: var(--ink);
  }
  .card__divider {
    position: absolute; left: 250px; top: 55px;
    width: 1px; height: 200px; background: var(--rule);
  }
  .contact {
    position: absolute; left: 268px; top: 70px; right: 16px;
    color: var(--ink-soft); font-size: 13px; line-height: 1.5;
    white-space: nowrap;
  }
  .contact__name {
    color: var(--brand-blue); font-weight: 700; font-size: 18px;
    letter-spacing: .02em; text-transform: uppercase; line-height: 1.2;
  }
  .contact__title { margin-bottom: 8px; }
  .contact__row { display: flex; align-items: center; gap: 6px; }
  .contact__row svg { width: 11px; height: 11px; fill: var(--brand-blue); flex: none; }
  .contact__address { margin-top: 10px; }

  /* Back */
  .card--back { left: 620px; background: var(--brand-blue); color: var(--paper); }
  .globe-art {
    position: absolute; right: -70px; top: -40px;
    width: 290px; height: 290px; border-radius: 50%;
    background: radial-gradient(circle at 40% 40%, var(--brand-blue-light), rgba(95,179,230,.35) 70%, rgba(95,179,230,0) 100%);
  }
  .back-lockup {
    position: absolute; left: 170px; top: 40px;
    display: flex; align-items: center; gap: 12px;
  }
  .back-lockup__dot {
    width: 62px; height: 62px; border-radius: 50%;
    background: var(--paper); flex: none;
  }
  .back-lockup__name { font-size: 18px; line-height: 1.05; font-weight: 400; }
  .services {
    position: absolute; left: 28px; top: 150px;
    list-style: none; font-size: 13.5px; line-height: 1.35;
  }
  .availability {
    position: absolute; right: 28px; bottom: 30px;
    text-align: right; font-size: 13.5px; line-height: 1.5;
  }
</style>
</head>
<body>
  <section class="card card--front" aria-label="Business card front">
    <div class="brand-lockup">
      <div class="brand-lockup__dot"></div>
      <div class="brand-lockup__name">Corvana<br>Tongue<br>Works LLC</div>
    </div>
    <div class="card__divider"></div>
    <div class="contact">
      <p class="contact__name">Rhoda Pelling</p>
      <p class="contact__title">President</p>
      <p class="contact__row">
        <svg viewBox="0 0 24 24" aria-hidden="true"><path d="M6.6 10.8a15.1 15.1 0 0 0 6.6 6.6l2.2-2.2c.3-.3.7-.4 1-.2 1.1.4 2.3.6 3.6.6.6 0 1 .4 1 1V20c0 .6-.4 1-1 1A17 17 0 0 1 3 4c0-.6.4-1 1-1h3.5c.6 0 1 .4 1 1 0 1.3.2 2.5.6 3.6.1.3 0 .7-.2 1z"/></svg>
        (555) 481-3062
      </p>
      <p class="contact__row">
        <svg viewBox="0 0 24 24" aria-hidden="true"><path d="M2 5h20v14H2z M2 5l10 8 10-8" fill-rule="evenodd"/></svg>
        rmpelling@corvanatongueworks.example
      </p>
      <p class="contact__row">
        <svg viewBox="0 0 24 24" aria-hidden="true"><circle cx="12" cy="12" r="11"/></svg>
        www.corvanatongue.example
      </p>
      <p class="contact__address">482 Garnet Ave., Ste. 219<br>Indianapolis, IN 40917 USA</p>
    </div>
  </section>

  <section class="card card--back" aria-label="Business card back">
    <div class="globe-art" role="img" aria-label="Faint globe with world map"></div>
    <div class="back-lockup">
      <div class="back-lockup__dot"></div>
      <div class="back-lockup__name">Corvana<br>Tongue<br>Works LLC</div>
    </div>
    <ul class="services">
      <li>ESL / ENL Language Classes, Private Lessons, and Online Tutors</li>
      <li>PLEXA Training and Testing</li>
      <li>Translating &amp; Interpreting Services</li>
      <li>Contact us about Over-the-Phone Interpreting in over 200 languages</li>
    </ul>
    <div class="availability">
      <p>24/7/365</p>
      <p>www.corvanatongue.example</p>
    </div>
  </section>
</body>
</html>
```